BorrowNest Website design, we are a home loan / lending company

We are a finance broking company that can do mortgages / home loans, Car Loans, Commercial Loans, SMSF Loans, Business Loans, Personal Loans
We are looking for a simple website, not too busy, easy to navigate, something that prompts customers to action or call us.
I like the simplicity of the following websites:
https://www.velkarafinance.com.au/ - I like this website front page. I was thinking I have my logo, the one with the black background appear , then the toolbar at the top perhaps?
https://trevix.com.au/business-loans# - on this page there are images under finance that works for you that I like that concept.
https://dunmerel.com.au/contact/ - I like the Make an Appointment page
https://trevix.com.au/about-us - Simple but effective page design

Target Market(s)

Home Loan Customer

Industry/Entity Type

Finance / Home Loans

Coding

Coded - Design and coding required

Number of Pages Required

5+ page

Font styles to use
Serif

Colors
0094D4
00A9DD
6FCCEA
C7EBF8
E9F6FB

Requirements
Must have
• The following Heading s - Contact Us, About Us, Our People, Make an Appointment, Loan Options, Calculators, Reviews. I want to use the Logo colours I have in the zip files I uploaded.
Nice to have
• Simple clean design

```html
<!DOCTYPE html>
<html lang="en">
<head>
<meta charset="utf-8">
<title>BorrowNest – Home Loans &amp; Lending</title>
<link rel="stylesheet" href="https://fonts.googleapis.com/css2?family=Montserrat:wght@600;700&family=Roboto:wght@400;500;700&display=swap">
<style>
:root{
  --blue:#0094D4;
  --blue-2:#00A9DD;
  --blue-3:#6FCCEA;
  --blue-4:#C7EBF8;
  --blue-5:#E9F6FB;
  --ink:#111;
  --text:#666;
  --dark:#121212;
  --white:#fff;
}
*{box-sizing:border-box;margin:0;padding:0}
html,body{width:1200px;height:3789px;overflow:hidden}
body{position:relative;font-family:"Roboto",sans-serif;color:var(--ink);background:var(--white)}
.abs{position:absolute}
.head-font{font-family:"Montserrat",sans-serif}

/* header */
.topbar{left:0;top:0;width:1200px;height:68px;background:var(--white)}
.brand{left:110px;top:14px;font-family:"Montserrat",sans-serif;font-weight:700;font-size:32px;color:#333;letter-spacing:-.5px}
.btn{display:inline-flex;align-items:center;gap:8px;font-weight:700;font-size:12px;color:#fff;text-transform:uppercase;border-radius:3px;letter-spacing:.2px}
.btn-appt{left:620px;top:16px;height:38px;padding:0 14px;background:var(--blue-2)}
.phone{left:894px;top:22px;display:flex;align-items:center;gap:16px;font-weight:700;font-size:18px;color:var(--blue)}
.phone .dot{width:28px;height:28px;border-radius:50%;background:var(--blue);display:flex;align-items:center;justify-content:center}
.nav{left:0;top:68px;width:1200px;height:47px;background:var(--blue);display:flex;justify-content:center;align-items:center;gap:44px}
.nav a{color:#fff;font-weight:700;font-size:13.5px;text-decoration:none;text-transform:uppercase}

/* hero */
.hero-photo{left:0;top:115px;width:1200px;height:701px;background:linear-gradient(100deg,#6c7176 0%,#8c9298 35%,#c3c8cc 60%,#5b6670 80%,#2d3b4f 100%)}
.hero-welcome{left:110px;top:244px;font-family:"Montserrat",sans-serif;font-weight:700;font-size:34px;color:#fff}
.hero-title{left:106px;top:288px;font-family:"Montserrat",sans-serif;font-weight:700;font-size:66px;color:#fff;letter-spacing:-1px}
.hero-lead{left:112px;top:388px;width:460px;font-weight:700;font-size:15px;line-height:24px;color:#fff}
.hero-btn1{left:112px;top:460px;height:41px;padding:0 14px;background:var(--blue-3)}
.hero-btn2{left:352px;top:460px;height:41px;padding:0 22px;background:var(--blue)}

/* about */
.about-photo{left:113px;top:838px;width:426px;height:426px;border-radius:50%;background:radial-gradient(circle at 45% 40%,#b9a58f,#6a5d52 60%,#3b3b3b)}
.about-heading{left:637px;top:872px;font-size:35px}
.accent{color:var(--blue-2)}
.rule{width:36px;height:3px;background:var(--blue)}
.about-text{left:637px;top:948px;width:450px;font-size:14px;line-height:24px;color:var(--text);text-align:justify}
.about-btn{left:637px;top:1184px;height:40px;padding:0 24px;background:var(--blue)}

/* services */
.services-heading{left:0;top:1398px;width:1200px;text-align:center;font-size:33px}
.svc{width:260px;text-align:center}
.svc-ring{width:220px;height:220px;margin:0 auto;border-radius:50%;background:linear-gradient(145deg,var(--blue-3),var(--blue) 70%);display:flex;align-items:center;justify-content:center;box-shadow:6px 10px 12px rgba(0,0,0,.22)}
.svc-core{width:180px;height:180px;border-radius:50%;background:var(--blue-5);display:flex;align-items:center;justify-content:center}
.svc h3{margin-top:14px;font-family:"Montserrat",sans-serif;font-weight:700;font-size:26px;color:#111}
.svc-desc{left:430px;top:2108px;width:340px;text-align:center;font-size:14px;line-height:24px;color:var(--text)}
.svc-more{left:0;top:2196px;width:1200px;text-align:center;font-weight:700;font-size:14px;color:var(--blue);text-decoration:underline}

/* testimonials */
.clients-heading{left:0;top:2445px;width:1200px;text-align:center;font-size:34px}
.quote{top:2540px;width:314px;height:125px;border-radius:14px;background:#fff;box-shadow:0 2px 10px rgba(0,0,0,.12);padding:30px 26px;font-style:italic;font-size:13.5px;line-height:23px;color:#555}
.quote.featured{background:var(--blue);color:#fff}
.quote .mark{position:absolute;right:26px;bottom:20px;font-family:Georgia,serif;font-size:44px;font-weight:700;line-height:20px;color:var(--blue)}
.quote.featured .mark{color:#fff}
.person{top:2692px;display:flex;gap:16px;align-items:center}
.avatar{width:58px;height:58px;border-radius:50%;background:linear-gradient(160deg,#d9c3a5,#8b7a6a)}
.person b{font-size:14px}
.person span{font-size:14px;font-weight:700;color:#555}
.rating{display:flex;gap:2px;margin-top:6px}
.rating i{width:10px;height:10px;background:#00b67a}

/* contact */
.contact{left:0;top:2846px;width:1200px;height:560px;background:linear-gradient(90deg,#0a8fd0,#0aa2dc)}
.contact-heading{left:0;top:2890px;width:1200px;text-align:center;font-size:34px;color:#fff}
.field{left:110px;width:462px;height:47px;background:#fff;font-size:15px;color:#777;padding:14px 22px}
.field-msg{left:584px;top:2985px;width:503px;height:168px;background:#fff;font-size:15px;color:#777;padding:14px 22px}
.submit{left:584px;top:3165px;width:144px;height:48px;border-radius:24px;background:#222;color:#fff;font-weight:700;font-size:14px;display:flex;align-items:center;justify-content:center}

/* footer */
.footer-brand{left:110px;top:3566px;font-family:"Montserrat",sans-serif;font-weight:700;font-size:36px;color:#fff}
.foot-title{font-weight:700;font-size:13.5px;color:#fff;padding-bottom:14px;border-bottom:1px solid #777}
.foot-links{list-style:none;font-size:14px;color:#fff}
.foot-links li{height:34.5px}
.foot-links li::before{content:"»";margin-right:18px}
.newsletter-text{left:801px;top:3530px;font-size:14px;color:#fff}
.news-input{left:803px;top:3566px;width:284px;height:47px;background:#fff;display:flex;align-items:center;justify-content:space-between;padding-left:16px;font-size:14px;color:#777}
.news-input .go{width:42px;height:43px;margin-right:2px;background:var(--blue);display:flex;align-items:center;justify-content:center}
.socials{left:803px;top:3642px;display:flex;gap:10px}
.socials i{width:35px;height:35px;border:1px solid #fff;border-radius:50%;display:block}
.legal{left:0;top:3735px;width:1200px;height:54px;background:var(--blue);color:#fff;font-size:14px}
.legal .l{position:absolute;left:106px;top:18px}
.legal .r{position:absolute;left:914px;top:18px;display:flex;gap:10px;align-items:center}
</style>
</head>
<body>

<!-- header -->
<div class="abs topbar"></div>
<div class="abs brand">BorrowNest</div>
<div class="abs btn btn-appt">Schedule an appointment
  <svg width="13" height="13" viewBox="0 0 13 13"><rect x="1" y="2" width="11" height="10" fill="none" stroke="#fff" stroke-width="1.5"/><line x1="1" y1="5" x2="12" y2="5" stroke="#fff" stroke-width="1.5"/></svg>
</div>
<div class="abs phone"><span class="dot"><svg width="14" height="14" viewBox="0 0 24 24"><path d="M6.6 10.8a15 15 0 006.6 6.6l2.2-2.2c.3-.3.7-.4 1-.2 1.1.4 2.3.6 3.6.6.6 0 1 .4 1 1V20c0 .6-.4 1-1 1A17 17 0 013 4c0-.6.4-1 1-1h3.5c.6 0 1 .4 1 1 0 1.3.2 2.5.6 3.6.1.3 0 .7-.2 1z" fill="#fff"/></svg></span>+ 1 800 555 0142</div>
<nav class="abs nav">
  <a href="#">&#x21bb;&nbsp; Home</a><a href="#">Contact Us</a><a href="#">About Us</a><a href="#">Our People</a><a href="#">Loan Options</a><a href="#">Calculators</a><a href="#">Reviews</a>
</nav>

<!-- hero -->
<div class="abs hero-photo" role="img" aria-label="Photo of a young businessman in glasses and suit reviewing a financial chart document"></div>
<svg class="abs" style="left:0;top:115px" width="1200" height="720" viewBox="0 0 1200 720">
  <path d="M0 402 C120 560 360 720 640 700 C900 680 1080 560 1200 456 L1200 720 L0 720 Z" fill="#fff"/>
  <path d="M0 402 C120 560 360 720 640 700 C900 680 1080 560 1200 456 L1200 480 C1080 590 900 700 640 720 C380 740 110 590 0 440 Z" fill="#0094D4"/>
</svg>
<div class="abs hero-welcome">Welcome To</div>
<div class="abs hero-title">BorrowNest</div>
<p class="abs hero-lead">Lorem ipsum dolor sit amet, consectetur adipiscing elit, sed do eiusmod tempor incididunt ut labore</p>
<div class="abs btn hero-btn1">Schedule an appointment &#9638;</div>
<div class="abs btn hero-btn2">Get started &nbsp;&#10148;</div>

<!-- about -->
<div class="abs about-photo" role="img" aria-label="Photo of a smiling young couple looking at a laptop together"></div>
<h2 class="abs head-font about-heading">About <span class="accent">Us</span></h2>
<div class="abs rule" style="left:637px;top:926px"></div>
<p class="abs about-text">Sed ut perspiciatis unde omnis iste natus error sit voluptatem accusantium doloremque laudantium, totam rem aperiam, eaque ipsa quae ab illo inventore veritatis et quasi architecto beatae vitae dicta sunt explicabo. Nemo enim ipsam voluptatem quia voluptas sit aspernatur aut odit aut fugit, sed quia consequuntur magni dolores eos qui ratione voluptatem sequi nesciunt.Sed ut perspiciatis unde omnis iste natus error sit voluptatem accusantium doloremque laudantium, totam rem aperiam, eaque ipsa quae ab illo inventore veritatis</p>
<div class="abs btn about-btn">Learn more &nbsp;&#10148;</div>

<!-- services band -->
<svg class="abs" style="left:0;top:1280px" width="1200" height="1110" viewBox="0 0 1200 1110">
  <path d="M0 190 C200 40 520 -10 760 40 C980 90 1130 230 1200 310 L1200 820 C1050 960 800 1090 560 1100 C320 1110 100 1000 0 850 Z" fill="#E9F6FB"/>
  <path d="M190 110 C380 10 620 -10 800 40 C1000 90 1140 240 1200 300 L1200 350 C1120 250 960 110 780 70 C600 30 380 40 190 110 Z" fill="#0094D4"/>
  <path d="M0 800 C100 950 320 1080 560 1102 C790 1115 1000 1030 1200 870 L1200 860 C1000 1000 800 1075 560 1072 C320 1060 120 960 0 840 Z" fill="#0094D4"/>
</svg>
<h2 class="abs head-font services-heading">Our <span class="accent">Services</span></h2>
<div class="abs rule" style="left:582px;top:1456px"></div>

<div class="abs svc" style="left:129px;top:1500px">
  <div class="svc-ring"><div class="svc-core">
    <svg width="100" height="100" viewBox="0 0 100 100"><path d="M10 48 L50 14 L90 48" fill="none" stroke="#0094D4" stroke-width="9" stroke-linejoin="round"/><rect x="24" y="46" width="52" height="42" fill="#0094D4"/><circle cx="50" cy="66" r="15" fill="#fff"/><text x="50" y="73" text-anchor="middle" font-family="Roboto,sans-serif" font-weight="700" font-size="20" fill="#0094D4">$</text></svg>
  </div></div><h3>Home Loan</h3>
</div>
<div class="abs svc" style="left:470px;top:1500px">
  <div class="svc-ring"><div class="svc-core">
    <svg width="120" height="100" viewBox="0 0 120 100"><path d="M10 78 L10 62 L28 50 L84 50 L110 62 L110 78 Z" fill="#0094D4"/><circle cx="32" cy="80" r="9" fill="#fff" stroke="#0094D4" stroke-width="5"/><circle cx="90" cy="80" r="9" fill="#fff" stroke="#0094D4" stroke-width="5"/><circle cx="86" cy="30" r="22" fill="#0094D4"/><text x="86" y="39" text-anchor="middle" font-family="Roboto,sans-serif" font-weight="700" font-size="26" fill="#fff">$</text></svg>
  </div></div><h3>Car Loans</h3>
</div>
<div class="abs svc" style="left:810px;top:1500px">
  <div class="svc-ring"><div class="svc-core">
    <svg width="100" height="100" viewBox="0 0 100 100"><path d="M30 40 L56 18 L82 40 L82 66 L30 66 Z" fill="none" stroke="#0094D4" stroke-width="6"/><text x="56" y="60" text-anchor="middle" font-family="Roboto,sans-serif" font-weight="700" font-size="26" fill="#0094D4">$</text><rect x="10" y="66" width="10" height="24" fill="#0094D4"/><path d="M24 72 L60 72 L86 62 L90 70 L62 88 L24 88 Z" fill="#0094D4"/></svg>
  </div></div><h3>Commercial Loans</h3>
</div>
<div class="abs svc" style="left:129px;top:1799px">
  <div class="svc-ring"><div class="svc-core">
    <svg width="100" height="100" viewBox="0 0 100 100"><path d="M22 46 L54 14 L86 46 L86 70 L22 70 Z" fill="#0094D4"/><text x="54" y="56" text-anchor="middle" font-family="Roboto,sans-serif" font-weight="700" font-size="26" fill="#fff">%</text><rect x="10" y="72" width="10" height="22" fill="#0094D4"/><path d="M24 76 L64 76 L88 66 L92 74 L66 92 L24 92 Z" fill="#0094D4"/></svg>
  </div></div><h3>SMSF Loans</h3>
</div>
<div class="abs svc" style="left:470px;top:1799px">
  <div class="svc-ring"><div class="svc-core">
    <svg width="100" height="100" viewBox="0 0 100 100"><circle cx="56" cy="30" r="22" fill="#0094D4"/><text x="56" y="40" text-anchor="middle" font-family="Roboto,sans-serif" font-weight="700" font-size="28" fill="#fff">$</text><rect x="12" y="64" width="10" height="26" fill="#0094D4"/><path d="M26 68 L62 68 L88 58 L92 66 L64 88 L26 88 Z" fill="#0094D4"/></svg>
  </div></div><h3>Business Loans</h3>
</div>
<div class="abs svc" style="left:810px;top:1799px">
  <div class="svc-ring"><div class="svc-core">
    <svg width="110" height="100" viewBox="0 0 110 100"><circle cx="55" cy="26" r="14" fill="#0094D4"/><circle cx="30" cy="34" r="10" fill="#0094D4"/><circle cx="80" cy="34" r="10" fill="#0094D4"/><path d="M10 56 L40 48 L55 60 L70 48 L100 56 L100 72 L72 92 L55 78 L38 92 L10 72 Z" fill="#0094D4"/></svg>
  </div></div><h3>Personal Loans</h3>
</div>
<div class="abs rule" style="left:582px;top:2084px;width:40px"></div>
<p class="abs svc-desc">Sed ut perspiciatis unde omnis iste natus error sivoluptatemaccusantidoloremque laudantium, totam rem aperiam, eaque</p>
<div class="abs svc-more">LEARN MORE &nbsp;&#10148;</div>

<!-- testimonials -->
<h2 class="abs head-font clients-heading">What Our <span class="accent">Clients Say</span></h2>
<div class="abs quote" style="left:106px">Sed ut perspiciatis unde omnis istenatus error sit voluptatem accusandoloremque laudantium, totam aperiam<span class="mark">&ldquo;</span></div>
<div class="abs quote featured" style="left:444px">Sed ut perspiciatis unde omnis istenatus error sit voluptatem accusandoloremque laudantium, totam aperiam<span class="mark">&ldquo;</span></div>
<div class="abs quote" style="left:779px">Sed ut perspiciatis unde omnis istenatus error sit voluptatem accusandoloremque laudantium, totam aperiam<span class="mark">&ldquo;</span></div>
<div class="abs person" style="left:120px"><div class="avatar" role="img" aria-label="Client portrait"></div><div><b>JOHN DOE ,</b> <span>Businessman</span><div class="rating"><i></i><i></i><i></i><i></i><i></i></div></div></div>
<div class="abs person" style="left:457px"><div class="avatar" role="img" aria-label="Client portrait"></div><div><b>JOHN DOE ,</b> <span>Businessman</span><div class="rating"><i></i><i></i><i></i><i></i><i></i></div></div></div>
<div class="abs person" style="left:793px"><div class="avatar" role="img" aria-label="Client portrait"></div><div><b>JOHN DOE ,</b> <span>Businessman</span><div class="rating"><i></i><i></i><i></i><i></i><i></i></div></div></div>

<!-- contact -->
<div class="abs contact"></div>
<h2 class="abs head-font contact-heading">Get In Touch</h2>
<div class="abs field" style="top:2985px">Name</div>
<div class="abs field" style="top:3045px">Email address</div>
<div class="abs field" style="top:3105px">Company Name</div>
<div class="abs field" style="top:3166px">Title / Position</div>
<div class="abs field-msg">How can we help ?</div>
<div class="abs submit">SUBMIT NOW</div>

<!-- footer -->
<svg class="abs" style="left:0;top:3260px" width="1200" height="480" viewBox="0 0 1200 480">
  <path d="M0 270 C260 60 560 10 800 20 C1000 30 1130 120 1200 200 L1200 480 L0 480 Z" fill="#3a3a3a"/>
  <path d="M0 280 C260 90 560 40 800 50 C1000 60 1120 150 1200 230 L1200 480 L0 480 Z" fill="#121212"/>
</svg>
<div class="abs footer-brand">BorrowNest</div>
<div class="abs foot-title" style="left:425px;top:3476px;width:297px">LINKS</div>
<ul class="abs foot-links" style="left:425px;top:3526px"><li>Home</li><li>About us</li><li>What We Do</li><li>Our people</li><li>Contact</li></ul>
<ul class="abs foot-links" style="left:604px;top:3526px"><li>FAQ</li><li>Loan Options</li><li>Privacy Policy</li><li>Terms Of Use</li><li>Help Service</li></ul>
<div class="abs foot-title" style="left:801px;top:3476px;width:280px">NEWSLETTER</div>
<div class="abs newsletter-text">Send us a newsletter to get update</div>
<div class="abs news-input">Email Address<span class="go"><svg width="16" height="16" viewBox="0 0 16 16"><path d="M1 7 L15 1 L10 15 L7 9 Z" fill="none" stroke="#fff" stroke-width="1.5"/></svg></span></div>
<div class="abs socials"><i></i><i></i><i></i><i></i></div>
<div class="abs legal"><span class="l">© 2022 BorrowNest . All Rights Reserved</span><span class="r"><svg width="16" height="12" viewBox="0 0 16 12"><rect x="0.5" y="0.5" width="15" height="11" fill="#fff"/><path d="M1 1 L8 7 L15 1" fill="none" stroke="#0094D4" stroke-width="1.3"/></svg>info@borrownest.com</span></div>

</body>
</html>
```